Satchel & Sundial needs new business card design

I need a new business card design. I'm looking for out-of-the-box design which represents the freedom of being a location independent entrepreneur.
I offer coaching, retreats and trips.
I would like to see designs with and without the photo.
Colors I use are black (#000000), green (#25A796) and brown (#D7C38C)
Website satchelandsundial.example

Target Market(s)

location independent entrepreneurs, digital nomads, people looking to swap the 9 to 5 for a lifestyle business

Industry/Entity Type

Business

Contact Information for Business Card

Dorota Falkner
Your Lifestyle Business Coach, Retreat & Trip Leader
http://satchelandsundial.example
hello@satchelandsundial.example
Live a life you don't need a holiday from

Font styles to use
Serif
Sans Serif

Requirements
Must have
• One side should contain only the logo. I would also consider having the "Live a life you don't need a holiday from" on that side too (depending on how it looks)
• Please show both sides on the designs.

```html
<!DOCTYPE html>
<html lang="en">
<head>
<meta charset="utf-8">
<title>Satchel &amp; Sundial — Business Card</title>
<link rel="stylesheet" href="https://fonts.googleapis.com/css2?family=Source+Sans+3:ital,wght@0,400;0,600;0,700;1,700&display=swap">
<style>
  :root {
    --ink: #1d1b19;
    --teal: #25a796;
    --sand: #d7c38c;
    --sand-deep: #cdb67a;
    --paper-white: #ffffff;
    --backdrop: #2b2a29;
  }
  html, body {
    margin: 0;
    width: 1200px;
    height: 987px;
    overflow: hidden;
    background: var(--backdrop);
    font-family: "Source Sans 3", "Myriad Pro", sans-serif;
  }
  .stage {
    position: relative;
    width: 1200px;
    height: 987px;
  }
  .card {
    position: absolute;
    left: 293px;
    width: 615px;
    height: 352px;
    background: var(--sand);
    overflow: hidden;
    box-shadow: 0 2px 6px rgba(0,0,0,.45);
  }
  .card--front { top: 130px; }
  .card--back  { top: 505px; }

  .wave {
    position: absolute;
    inset: 0;
    width: 100%;
    height: 100%;
  }
  .wordmark {
    position: absolute;
    margin: 0;
    color: var(--ink);
    font-weight: 600;
    letter-spacing: .5px;
    white-space: nowrap;
    line-height: 1;
  }
  .card--front .wordmark {
    left: 47px;
    top: 50px;
    font-size: 34px;
  }
  .card--back .wordmark {
    left: 0;
    right: 0;
    top: 175px;
    text-align: center;
    font-size: 44px;
  }
  .contact {
    position: absolute;
    right: 39px;
    top: 176px;
    text-align: right;
    color: var(--paper-white);
    line-height: 1.3;
  }
  .contact__name {
    margin: 0;
    font-size: 20px;
    font-weight: 600;
  }
  .contact__role {
    margin: 1px 0 0;
    font-size: 16.5px;
    font-weight: 400;
  }
  .contact__links {
    margin: 12px 0 0;
    font-size: 16px;
    font-weight: 400;
  }
  .contact__links a {
    color: inherit;
    text-decoration: none;
    display: block;
  }
  .contact__motto {
    margin: 9px 0 0;
    font-size: 16.5px;
    font-weight: 700;
    font-style: italic;
  }
  .backdrop-pattern {
    position: absolute;
    inset: 0;
    background: linear-gradient(160deg, var(--sand) 0%, var(--sand-deep) 50%, var(--sand) 100%);
  }
</style>
</head>
<body>
<main class="stage">
  <section class="card card--front" aria-label="Card front">
    <svg class="wave" viewBox="0 0 615 352" aria-hidden="true">
      <path d="M0,233 C60,292 120,312 200,292 C300,262 380,80 504,75 C560,73 600,95 615,104 L615,352 L0,352 Z" fill="var(--teal)"/>
      <g fill="none" stroke="var(--ink)">
        <path d="M0,226 C60,288 120,309 200,288 C300,258 380,74 504,69 C560,67 600,89 615,98" stroke-width="6"/>
        <path d="M0,233 C60,292 120,312 200,292 C300,262 380,80 504,75 C560,73 600,95 615,104" stroke-width="1.2"/>
      </g>
    </svg>
    <h1 class="wordmark">Satchel &amp; Sundial</h1>
    <div class="contact">
      <p class="contact__name">Dorota Falkner</p>
      <p class="contact__role">Your Lifestyle Business Coach<br>Retreat &amp; Trip Leader</p>
      <p class="contact__links">
        <a href="mailto:hello@satchelandsundial.example">hello@satchelandsundial.example</a>
        <a href="http://satchelandsundial.example">www.satchelandsundial.example</a>
      </p>
      <p class="contact__motto">Live a life you don't need a holiday from</p>
    </div>
  </section>

  <section class="card card--back" aria-label="Card back">
    <div class="backdrop-pattern" role="img" aria-label="Faint repeated brand pattern across the card"></div>
    <h2 class="wordmark">Satchel &amp; Sundial</h2>
  </section>
</main>
</body>
</html>
```